Album Cover Art for New Single

Independent singer-songwriter and pianist, seeking design work for a new single "Walk Beside the Lantern". Christian & Gospel music format. See attached for master recording.

This single is personal for me, so I'm looking for an image that really captures the heart of the message. Redemption, forgiveness, prodigals returning home to a loving father.
Updates

Target Market(s)

Millenials

Colors

Designer to choose colors to be used in the design.

Requirements
Must have
• simple graphic, must include the following text:
• Walk Beside the Lantern
• Dale Verrick
Should not have
• Avoid "cheesy" look and feel.

```html
<!DOCTYPE html>
<html lang="en">
<head>
<meta charset="utf-8">
<title>Walk Beside the Lantern — Dale Verrick</title>
<link href="https://fonts.googleapis.com/css2?family=Amatic+SC:wght@400;700&family=Cinzel:wght@600&display=swap" rel="stylesheet">
<style>
  :root {
    --fog-top: #c9c7c2;
    --fog-mid: #b6b0a5;
    --field-rust: #8c6b4b;
    --field-olive: #7a6a4c;
    --field-dark: #5f4c36;
    --text-light: #ffffff;
  }
  html, body {
    margin: 0;
    padding: 0;
    width: 1200px;
    height: 1200px;
    overflow: hidden;
    background: var(--fog-top);
  }
  .cover {
    position: relative;
    width: 1200px;
    height: 1200px;
    overflow: hidden;
  }
  .cover-backdrop {
    position: absolute;
    inset: 0;
    background: linear-gradient(180deg,
      var(--fog-top) 0%,
      var(--fog-top) 32%,
      var(--fog-mid) 46%,
      var(--field-rust) 60%,
      var(--field-olive) 80%,
      var(--field-dark) 100%);
  }
  .single-title {
    position: absolute;
    top: 140px;
    left: 0;
    width: 1200px;
    margin: 0;
    text-align: center;
    font-family: "Amatic SC", cursive;
    font-weight: 700;
    font-size: 228px;
    line-height: 188px;
    letter-spacing: 4px;
    color: var(--text-light);
    text-transform: uppercase;
  }
  .single-title span {
    display: block;
  }
  .artist-name {
    position: absolute;
    top: 1106px;
    left: 0;
    width: 1200px;
    margin: 0;
    padding-left: 0.7em;
    box-sizing: border-box;
    text-align: center;
    font-family: "Cinzel", serif;
    font-weight: 600;
    font-size: 26px;
    letter-spacing: 0.7em;
    color: var(--text-light);
    text-transform: uppercase;
  }
</style>
</head>
<body>
  <main class="cover">
    <div class="cover-backdrop" role="img" aria-label="Photograph of a person walking up a narrow dirt path through dry brown grass toward a foggy line of bare trees"></div>
    <h1 class="single-title">
      <span>Walk</span>
      <span>Beside</span>
      <span>the</span>
      <span>Lantern</span>
    </h1>
    <p class="artist-name">Dale Verrick</p>
  </main>
</body>
</html>
```